Harborline Auto LLC

Car Dealer Customer Service
Address: 2874 Cresthaven Road, Shelbyville, TN 37162
web: www.harborlineautoxq.net
email: harborlineautoxq@mailnest.example
Phone: (931) 555-0148
Phone: (629) 555-0173

```html
<!DOCTYPE html>
<html lang="en">
<head>
<meta charset="utf-8">
<title>Harborline Auto – Business Card</title>
<link rel="stylesheet" href="https://fonts.googleapis.com/css2?family=Poppins:ital,wght@0,400;0,600;0,700;1,400&display=swap">
<style>
  :root {
    --page-bg: #e7e3de;
    --card-bg: #f3f5f6;
    --brand-blue: #1f7ea6;
    --band-blue: #2a8bb7;
    --band-orange: #f0a732;
    --ink: #2b2f33;
    --white: #ffffff;
  }
  html, body {
    margin: 0;
    width: 1200px;
    height: 1054px;
    overflow: hidden;
    background: var(--page-bg);
    font-family: "Poppins", sans-serif;
  }
  .card {
    position: absolute;
    left: 100px;
    top: 226px;
    width: 1000px;
    height: 603px;
    background: var(--card-bg);
    border-radius: 22px;
    overflow: hidden;
    box-shadow: 0 10px 30px rgba(0,0,0,0.12);
  }
  .brand-title {
    position: absolute;
    left: 47px;
    top: 58px;
    margin: 0;
    font-size: 70px;
    font-weight: 700;
    letter-spacing: 1px;
    color: var(--brand-blue);
    line-height: 1;
  }
  .band-blue {
    position: absolute;
    left: 0; top: 190px;
    width: 100%; height: 226px;
    background: var(--band-blue);
  }
  .band-orange {
    position: absolute;
    left: 0; top: 416px;
    width: 100%; height: 98px;
    background: var(--band-orange);
  }
  .tagline {
    position: absolute;
    left: 47px; top: 226px;
    margin: 0;
    font-size: 26px;
    font-style: italic;
    color: var(--white);
  }
  .phones {
    position: absolute;
    left: 47px; top: 276px;
    margin: 0; padding: 0;
    list-style: none;
  }
  .phones li {
    display: flex;
    align-items: center;
    gap: 16px;
    height: 46px;
    font-size: 35px;
    font-weight: 600;
    color: var(--white);
    letter-spacing: 0.5px;
  }
  .contact-web {
    position: absolute;
    left: 47px; top: 424px;
    margin: 0; padding: 0;
    list-style: none;
  }
  .contact-web li {
    display: flex;
    align-items: center;
    gap: 22px;
    height: 38px;
    font-size: 25px;
    color: var(--ink);
  }
  .address {
    position: absolute;
    left: 47px; top: 520px;
    margin: 0;
    font-size: 27px;
    color: var(--ink);
  }
  .brand-mark {
    position: absolute;
    left: 566px; top: 185px;
    width: 320px; height: 320px;
    border-radius: 50%;
    background: var(--white);
    display: flex;
    align-items: center;
    justify-content: center;
    text-align: center;
  }
  .brand-mark span {
    font-size: 36px;
    font-weight: 700;
    color: var(--brand-blue);
    line-height: 1.15;
  }
  .icon { flex: none; }
</style>
</head>
<body>
  <main class="card">
    <h1 class="brand-title">HARBORLINE AUTO</h1>
    <div class="band-blue"></div>
    <div class="band-orange"></div>

    <p class="tagline">Car Dealer Customer Service</p>

    <ul class="phones">
      <li>
        <svg class="icon" width="30" height="26" viewBox="0 0 30 26" aria-hidden="true">
          <path d="M3 9 Q15 0 27 9 L24 12 L20 10 L20 7 Q15 5 10 7 L10 10 L6 12 Z" fill="#f0a732"/>
          <rect x="6" y="13" width="18" height="12" rx="2" fill="#f0a732"/>
          <circle cx="15" cy="19" r="3" fill="#2a8bb7"/>
        </svg>
        931-555-0148
      </li>
      <li>
        <svg class="icon" width="30" height="26" viewBox="0 0 30 26" aria-hidden="true">
          <path d="M3 9 Q15 0 27 9 L24 12 L20 10 L20 7 Q15 5 10 7 L10 10 L6 12 Z" fill="#f0a732"/>
          <rect x="6" y="13" width="18" height="12" rx="2" fill="#f0a732"/>
          <circle cx="15" cy="19" r="3" fill="#2a8bb7"/>
        </svg>
        629-555-0173
      </li>
    </ul>

    <ul class="contact-web">
      <li>
        <svg class="icon" width="22" height="16" viewBox="0 0 22 16" aria-hidden="true">
          <rect x="0" y="0" width="22" height="16" rx="1" fill="#2b2f33"/>
          <path d="M1 1 L11 9 L21 1" stroke="#f0a732" stroke-width="1.8" fill="none"/>
        </svg>
        www.harborlineautoxq.net
      </li>
      <li>
        <svg class="icon" width="22" height="22" viewBox="0 0 22 22" aria-hidden="true">
          <circle cx="11" cy="11" r="10" fill="#2b2f33"/>
          <ellipse cx="11" cy="11" rx="4" ry="10" fill="none" stroke="#f0a732" stroke-width="1.4"/>
          <path d="M1 11 H21 M3 6 H19 M3 16 H19" stroke="#f0a732" stroke-width="1.4"/>
        </svg>
        harborlineautoxq@mailnest.example
      </li>
    </ul>

    <p class="address">2874 Cresthaven Road, Shelbyville, TN 37162</p>

    <div class="brand-mark"><span>Harborline<br>Auto</span></div>
  </main>
</body>
</html>
```